TLK Electricial Contracting Services

Hi guys, after a design for my small electrical company, have logo design files to be incorporated into the layout, the basic concept is electrical contracting services for residential, commercial, industrial & data services, image is clean clear and strong,

Card format is to have a nice clean logo on front,with maybe the Residential – commercial – industrial - data, followed with licensed & insured, followed by contact details on backside of the card.

Target Market(s)

Residential, commercial, industrial sectors.

Industry/Entity Type

Electrical

Contact Information for Business Card

TLK logo,
Residential – commercial – industrial - data
REC: 61307
Email: tlk@vornamail.net.au
Phone: 0487 352 019

Requirements
Must have
• Clean & strong design.
Nice to have
• If possible, I would like the logo colours inverted so the text is orange and the background is black on the front of the card, then the backside of the card be the reverse colour
Should not have
• No Sparks, lightning bolts,

```html
<!DOCTYPE html>
<html lang="en">
<head>
<meta charset="utf-8">
<title>TLK Electricial Contracting Services – Business Card</title>
<link href="https://fonts.googleapis.com/css2?family=Lato:wght@400;700&display=swap" rel="stylesheet">
<style>
  :root {
    --backdrop: #1e1e1e;
    --card-black: #0d0d0d;
    --brand-orange: #f0802a;
    --text-white: #f2f2f2;
    --text-grey: #9a9a9a;
    --ink-black: #111111;
  }
  * { margin: 0; padding: 0; box-sizing: border-box; }
  html, body {
    width: 1200px;
    height: 900px;
    overflow: hidden;
    background: var(--backdrop);
    font-family: "Lato", Arial, sans-serif;
  }
  .stage {
    position: relative;
    width: 1200px;
    height: 900px;
  }
  .card {
    position: absolute;
    top: 232px;
    width: 252px;
    height: 430px;
    box-shadow: 2px 3px 6px rgba(0, 0, 0, 0.55);
    text-align: center;
  }
  .card--front {
    left: 336px;
    background: var(--card-black);
    color: var(--brand-orange);
  }
  .card--back {
    left: 630px;
    background: var(--brand-orange);
    color: var(--ink-black);
  }
  .brand {
    position: absolute;
    left: 0;
    right: 0;
    font-weight: 700;
    color: inherit;
    line-height: 1;
  }
  .card--front .brand { top: 60px; }
  .card--back .brand { top: 166px; }
  .brand__name {
    display: block;
    font-size: 60px;
    letter-spacing: 2px;
  }
  .brand__tagline {
    display: block;
    margin-top: 6px;
    font-size: 12.5px;
    letter-spacing: 0.3px;
  }
  .card--back .brand__name { font-size: 62px; }
  .services {
    position: absolute;
    top: 170px;
    left: 0;
    right: 0;
    list-style: none;
    color: var(--text-white);
    font-size: 12.5px;
    line-height: 15.7px;
  }
  .licence {
    position: absolute;
    top: 249px;
    left: 0;
    right: 0;
    color: var(--text-white);
    font-size: 12.5px;
  }
  .contact {
    position: absolute;
    top: 351px;
    left: 0;
    right: 0;
    list-style: none;
    color: var(--text-grey);
    font-size: 13px;
    line-height: 17px;
  }
  .contact__item {
    display: flex;
    align-items: center;
    justify-content: center;
    gap: 5px;
  }
  .contact__icon { width: 10px; height: 10px; fill: var(--brand-orange); }
</style>
</head>
<body>
<main class="stage">
  <section class="card card--front" aria-label="Card front">
    <div class="brand">
      <span class="brand__name">TLK</span>
      <span class="brand__tagline">Tom Lark Electrical</span>
    </div>
    <ul class="services">
      <li>RESIDENTIAL</li>
      <li>COMMERCIAL</li>
      <li>INDUSTRIAL</li>
      <li>DATA</li>
    </ul>
    <p class="licence">REC: 61307</p>
    <ul class="contact">
      <li class="contact__item">
        <svg class="contact__icon" viewBox="0 0 10 10" aria-hidden="true">
          <path d="M1 3.2C1 2 2.5 1 5 1s4 1 4 2.2v1H7V3.4H3v.8H1zM2.2 5L3.5 3.9h3L7.8 5v3.6H2.2zM5 5.3a1.3 1.3 0 1 0 0 2.6 1.3 1.3 0 0 0 0-2.6z"/>
        </svg>
        <span>0487 352 019</span>
      </li>
      <li class="contact__item">
        <svg class="contact__icon" viewBox="0 0 10 10" aria-hidden="true">
          <path d="M0.5 2h9v6h-9zM1.3 2.6L5 5.4l3.7-2.8z" fill-rule="evenodd"/>
        </svg>
        <span>tlk@vornamail.net.au</span>
      </li>
    </ul>
  </section>

  <section class="card card--back" aria-label="Card back">
    <div class="brand">
      <span class="brand__name">TLK</span>
      <span class="brand__tagline">Tom Lark Electrical</span>
    </div>
  </section>
</main>
</body>
</html>
```